Sales Page Header Design Project

Hi,
I need a background image created for this sales page: http://trimventurecamp.com
Width: 977 px
Height: 150 px
Here are a few sample designs to work with: http://firmsummitschool.com/
http://craftingamarkweb.com/wp-content/uploads/2011/02/experts1.png
Must be sharp, professional looking and uncluttered.
Colours: Must include blue (I like the blue on the on the current sales page, but will leave shade and colour combinations to your creativity)
Text = Tobi Wanrenu Presents
Trim Venture Camp
Your Blueprint for Building a Profitable, Sustainable Business in Today's Economy!
Any questions, give me a shout
Entrepreneurs and Business Owners, aged 21 to 45
Business

```html
<!DOCTYPE html>
<html lang="en">
<head>
<meta charset="utf-8">
<title>Trim Venture Camp – Sales Page Header</title>
<link rel="stylesheet" href="https://fonts.googleapis.com/css2?family=Arimo:ital,wght@0,400;0,700;1,400&display=swap">
<style>
  :root {
    --page-light: #ffffff;
    --page-edge: #c9c9c9;
    --band-center: #2a80bd;
    --band-mid: #1c5d8c;
    --band-edge: #0a2639;
    --presenter-grey: #b9c3ca;
    --title-white: #ffffff;
    --tagline-cyan: #3fdcf4;
    --icon-blue: #3aa8e0;
    --icon-dark: #4a4f55;
  }
  * { margin: 0; padding: 0; box-sizing: border-box; }
  html, body { width: 1200px; height: 1000px; overflow: hidden; }
  body {
    background: radial-gradient(ellipse 70% 70% at 50% 50%, var(--page-light) 55%, var(--page-edge) 100%);
    font-family: "Arimo", Arial, sans-serif;
    position: relative;
  }
  .header-band {
    position: absolute;
    left: 96px; top: 414px;
    width: 977px; height: 150px;
    background: radial-gradient(ellipse 60% 140% at 50% 40%, var(--band-center) 0%, var(--band-mid) 55%, var(--band-edge) 100%);
    text-align: center;
    color: var(--title-white);
  }
  .presenter {
    position: absolute;
    top: 22px; left: 0; right: 0;
    font-size: 15px;
    color: var(--presenter-grey);
    letter-spacing: 0.2px;
  }
  .presenter small {
    font-size: 9px;
    letter-spacing: 1.4px;
    margin-left: 2px;
  }
  .title-row {
    position: absolute;
    top: 50px; left: 0; right: 0;
    display: flex;
    justify-content: center;
    align-items: flex-end;
    gap: 8px;
    height: 62px;
  }
  .title {
    font-size: 50px;
    line-height: 62px;
    text-shadow: 2px 2px 3px rgba(0,0,0,0.55);
  }
  .title-light { font-weight: 400; }
  .title-bold { font-weight: 700; }
  .growth-icon { width: 64px; height: 62px; display: block; }
  .tagline {
    position: absolute;
    top: 114px; left: 0; right: 0;
    font-size: 15.5px;
    font-style: italic;
    color: var(--tagline-cyan);
    letter-spacing: 0.3px;
    text-shadow: 1px 1px 2px rgba(0,0,0,0.6);
  }
</style>
</head>
<body>
  <header class="header-band">
    <p class="presenter">Tobi Wanrenu <small>Presents</small></p>
    <div class="title-row">
      <span class="title title-light">Trim Venture</span>
      <svg class="growth-icon" viewBox="0 0 64 62" role="img" aria-label="Icon of a businessman beside rising bar chart with upward arrow">
        <defs>
          <linearGradient id="iconFill" x1="0" y1="0" x2="0" y2="1">
            <stop offset="0" stop-color="var(--icon-dark)"/>
            <stop offset="1" stop-color="var(--icon-blue)"/>
          </linearGradient>
        </defs>
        <rect x="2" y="2" width="60" height="56" rx="4" fill="url(#iconFill)" opacity="0.7"/>
      </svg>
      <span class="title title-bold">Camp</span>
    </div>
    <p class="tagline">Your Blueprint for Building a Profitable, Sustainable Business in Today's Economy!</p>
  </header>
</body>
</html>
```